Lark Vista Perks Needs a Website Design

We need a website design for a new service we are starting. Users enter a coupon in a redemption page and either create an account or sign in. they can then use the credits they accumulate from the coupons to purchase items listed on the site.

we need a design for the following:
-the coupon redemption page (with a choice to either sign in or create an account)
-a product listing page (with search filters and a search bar. the search bar can be displayed in the header of the site)
-a product detail page, showing the product's title, image, credit redemption value, brand and any category associated with the item
-a my account page, with:
*a list of the pluses (coupons/credit added to account) and the minuses (orders placed/credits subtracted from account) to show a detailed description of their history on the site)
*an area for users to edit their name, phone number, address etc
*an area for users to add / edit their casino membership number and casino
*an area for users to add a coupon to their account
-a cart / checkout process:
*cart displaying items and their total
*entering / selecting an address from their account
*review order details page where they can submit their order (and warning the user that doing so will subtract the required credits from their account)

remember that no ecommerce or money is used on the site.. users are spending their credits and checkout their cart with the credits they accumulated, so the items each have a credit redemption value and the checkout process is shown in credits.

we are not very particular with any design preference, other than we'd like it to be predominately white.

If designing the site with css please make sure to use bootstrap in your designs. thanks!

Target Market(s)

adults 45-65

Industry/Entity Type

Casino

Coding

Coded - Design and coding required

Number of Pages Required

5+ page

Font styles to use
Sans Serif

Requirements
Must have
• css must use with bootstrap
Nice to have
• simplified, easy interface. we are targeting an older crowd and dont want to confuse them
Should not have
• the site shouldnt have any dollar values. all product prices, checkout totals and user accrual's (in the my account page) should be in credits

```html
<!DOCTYPE html>
<html lang="en">
<head>
<meta charset="utf-8">
<title>Lark Vista Perks – Redemption</title>
<link rel="stylesheet" href="https://fonts.googleapis.com/css2?family=Open+Sans:wght@400;600;700&display=swap">
<style>
  :root {
    --white: #ffffff;
    --brand-blue: #0b67b2;
    --brand-red: #d0191c;
    --ink: #1d1d1d;
    --ink-soft: #444444;
    --muted: #6b6b6b;
    --divider: #dcdcdc;
    --hero-light: #e6edf6;
    --hero-mid: #c9d6ea;
    --hero-deep: #b7c6e0;
    --panel-frame: rgba(90, 100, 115, 0.72);
  }
  * { box-sizing: border-box; margin: 0; padding: 0; }
  html, body { width: 1200px; height: 650px; overflow: hidden; background: var(--white); }
  body { font-family: "Open Sans", Arial, sans-serif; color: var(--ink); position: relative; }

  .site-header { position: absolute; left: 0; top: 0; width: 1200px; height: 98px; background: var(--white); }
  .brand { position: absolute; left: 132px; top: 26px; display: flex; align-items: center; gap: 8px; }
  .brand-mark { width: 47px; height: 47px; border: 2px solid var(--brand-red); border-radius: 50%; }
  .brand-name { font-size: 25px; font-weight: 700; color: var(--brand-blue); letter-spacing: 0.2px; white-space: nowrap; }

  .header-nav { position: absolute; top: 32px; right: 132px; height: 37px; display: flex; align-items: center; white-space: nowrap; }
  .nav-link { font-size: 11.5px; font-weight: 700; color: var(--ink-soft); text-transform: uppercase; display: flex; align-items: center; gap: 7px; white-space: nowrap; }
  .nav-divider { width: 1px; height: 37px; background: var(--divider); margin: 0 14px 0 10px; flex: none; }
  .nav-button { height: 33px; padding: 0 10px; border: 1px solid; border-radius: 3px; font-size: 11.5px; font-weight: 700; text-transform: uppercase; display: flex; align-items: center; gap: 7px; white-space: nowrap; flex: none; }
  .nav-button--create { color: var(--brand-red); border-color: var(--brand-red); }
  .nav-button--signin { color: var(--brand-blue); border-color: var(--brand-blue); padding: 0 12px; }

  .hero { position: absolute; left: 0; top: 98px; width: 1200px; height: 490px; }
  .hero-backdrop { position: absolute; inset: 0; background: linear-gradient(135deg, var(--hero-mid) 0%, var(--hero-light) 40%, var(--hero-light) 60%, var(--hero-deep) 100%); }
  .hero-arrow { position: absolute; top: 219px; }
  .hero-arrow--prev { left: 118px; }
  .hero-arrow--next { left: 1069px; }
  .hero-title { position: absolute; top: 144px; width: 100%; text-align: center; font-size: 29px; font-weight: 700; color: var(--ink); letter-spacing: 0.5px; }
  .hero-lead { position: absolute; top: 190px; left: 255px; width: 690px; text-align: center; font-size: 14.4px; line-height: 26px; color: var(--ink-soft); }

  .coupon-form { position: absolute; left: 301px; top: 260px; width: 598px; height: 77px; background: var(--panel-frame); border-radius: 3px; padding: 12px 11px; display: flex; }
  .coupon-input { flex: 1; height: 52px; background: var(--white); border-radius: 3px 0 0 3px; padding-left: 23px; display: flex; align-items: center; font-size: 11px; color: var(--muted); text-transform: uppercase; }
  .coupon-submit { width: 90px; height: 52px; background: var(--brand-blue); color: var(--white); border-radius: 0 3px 3px 0; font-size: 12px; font-weight: 700; display: flex; align-items: center; justify-content: center; text-transform: uppercase; }

  .site-footer { position: absolute; left: 0; top: 588px; width: 1200px; height: 62px; background: var(--white); }
  .copyright { position: absolute; left: 134px; top: 23px; font-size: 11px; color: var(--muted); white-space: nowrap; }
  .social { position: absolute; left: 896px; top: 21px; display: flex; align-items: center; }
  .social-label { font-size: 11px; color: var(--muted); margin-right: 23px; white-space: nowrap; }
  .social-tile { width: 20px; height: 20px; border-radius: 3px; background: var(--brand-blue); margin-right: 11px; }
</style>
</head>
<body>
  <header class="site-header">
    <div class="brand">
      <span class="brand-mark"></span>
      <span class="brand-name">LARK VISTA PERKS</span>
    </div>
    <nav class="header-nav">
      <span class="nav-link">
        <svg width="10" height="10" viewBox="0 0 10 10"><path d="M1.5 7V5a3.5 3.5 0 0 1 7 0v2" fill="none" stroke="#444" stroke-width="1.4"/><rect x="0.8" y="5.5" width="2.2" height="3.5" rx="0.6" fill="#444"/><rect x="7" y="5.5" width="2.2" height="3.5" rx="0.6" fill="#444"/></svg>
        Customer Care
      </span>
      <span class="nav-divider"></span>
      <span class="nav-button nav-button--create">
        <svg width="11" height="10" viewBox="0 0 11 10"><path d="M0 4h5V1.5L9 5 5 8.5V6H0z" fill="#d0191c"/><path d="M7 0.8h3v8.4H7" fill="none" stroke="#d0191c" stroke-width="1.4"/></svg>
        Create an Account
      </span>
      <span class="nav-divider"></span>
      <span class="nav-button nav-button--signin">
        <svg width="11" height="10" viewBox="0 0 11 10"><path d="M0 4h5V1.5L9 5 5 8.5V6H0z" fill="#0b67b2"/><path d="M7 0.8h3v8.4H7" fill="none" stroke="#0b67b2" stroke-width="1.4"/></svg>
        Sign In
      </span>
    </nav>
  </header>

  <section class="hero">
    <div class="hero-backdrop" role="img" aria-label="Soft blue-toned photo of a desk with a laptop keyboard and hands at work"></div>
    <svg class="hero-arrow hero-arrow--prev" width="14" height="52" viewBox="0 0 14 52"><path d="M13 1 1 26l12 25" fill="none" stroke="#7d8796" stroke-width="1.2"/></svg>
    <svg class="hero-arrow hero-arrow--next" width="14" height="52" viewBox="0 0 14 52"><path d="M1 1l12 25L1 51" fill="none" stroke="#7d8796" stroke-width="1.2"/></svg>
    <h1 class="hero-title">REDEMPTION</h1>
    <p class="hero-lead">Cupiditate non provident, similique sunt in culpa qui officia deserunt mollitia animi, id est laborum<br>et dolorum fuga. Et harum quidem rerum...</p>
    <div class="coupon-form">
      <div class="coupon-input">Enter a coupon code</div>
      <div class="coupon-submit">Submit</div>
    </div>
  </section>

  <footer class="site-footer">
    <p class="copyright">Copyrights © 2017, Lark Vista Perks. All Rights Reserved</p>
    <div class="social">
      <span class="social-label">Follow us on :</span>
      <span class="social-tile"></span>
      <span class="social-tile"></span>
      <span class="social-tile"></span>
    </div>
  </footer>
</body>
</html>
```